Kestrada LLC, needs a web page no more than 5 pages (for now)

Kestrada is a general contractor. Our services include general contracting, design-build construction, disaster recovery and environmental remediation. Our main clients are PMX, TQ, State and Local Gov't Agencies, Hospitals and Schools. Kestrada is also a SDVOSB.

```html
<!DOCTYPE html>
<html lang="en">
<head>
<meta charset="utf-8">
<title>Kestrada LLC — General Contractor</title>
<link rel="stylesheet" href="https://fonts.googleapis.com/css2?family=Montserrat:wght@300;400;500;600;700;800&display=swap">
<style>
:root{
  --black:#000;
  --ink:#111;
  --panel:#1a1a1a;
  --white:#fff;
  --gold:#c8843a;
  --gold-light:#e3a865;
  --gold-pale:#f0c28a;
  --bronze:#a4541a;
  --muted:#bdbdbd;
}
*{margin:0;padding:0;box-sizing:border-box}
html,body{width:1200px;height:4286px;overflow:hidden;background:var(--black)}
body{position:relative;font-family:"Montserrat",sans-serif;color:var(--white)}
.abs{position:absolute}
a{color:inherit;text-decoration:none}

/* header */
.site-header{position:absolute;left:0;top:0;width:1200px;height:138px;background:var(--black);z-index:5}
.brand{position:absolute;left:152px;top:82px;display:flex;align-items:center;gap:10px;z-index:6;font-size:36px;font-weight:500;letter-spacing:1px;color:var(--gold-light)}
.brand-dot{width:16px;height:16px;border-radius:50%;background:var(--gold)}
.call-btn{position:absolute;left:804px;top:22px;width:251px;height:43px;border-radius:4px;background:linear-gradient(#e0a05a,#c07a34);display:flex;align-items:center;padding-left:12px;gap:10px;font-size:13px;color:#fff;z-index:6}
.call-icon{width:26px;height:26px;border-radius:50%;background:#fff;display:flex;align-items:center;justify-content:center}
.main-nav{position:absolute;top:96px;left:0;z-index:6;font-size:13.5px;font-weight:500}
.main-nav a{position:absolute;white-space:nowrap}
.main-nav .active::after{content:"";position:absolute;left:0;right:0;top:28px;height:3px;background:var(--gold)}

/* hero */
.hero-photo{position:absolute;left:0;top:138px;width:1200px;height:720px;background:radial-gradient(ellipse 520px 420px at 600px 620px,#8c9aa6 0%,#6a6560 40%,#3a2a1e 70%,#140c07 100%)}
.hero-title{position:absolute;left:0;width:1200px;text-align:center;font-weight:800;font-size:44px;line-height:52px;letter-spacing:.5px;top:228px}
.hero-title .accent{color:var(--gold);font-weight:500}
.btn-gold{position:absolute;display:flex;align-items:center;justify-content:center;border-radius:4px;background:linear-gradient(#e3a45c,#bf7632);font-weight:700;font-size:13.5px;color:#fff;letter-spacing:.3px}
.hero-dots span{position:absolute;left:1122px;width:9px;height:9px;border-radius:50%;background:#fff}
.hero-dots span.on{background:var(--gold-light)}

/* section titles */
.section-title{position:absolute;font-size:46px;line-height:1;white-space:nowrap;letter-spacing:.5px}
.section-title b{font-weight:800}
.section-title span{font-weight:400;color:var(--gold-light)}
.section-title::before{content:"";position:absolute;left:-16px;top:-22px;width:64px;height:64px;border-radius:50%;border:3px solid transparent;border-top-color:#ddd;border-left-color:#ddd;transform:rotate(10deg)}

/* about */
.about-art{position:absolute;left:145px;top:965px;width:455px;height:430px;border-radius:8px;background:radial-gradient(ellipse 220px 200px at 60% 55%,#5a3d22 0%,#2a1d12 55%,#000 100%)}
.about-badge{position:absolute;left:208px;top:1030px;width:176px;height:176px;border-radius:50%;background:#f2f2f2}
.about-text{position:absolute;left:642px;top:1042px;width:412px;font-size:14.5px;line-height:31.2px;text-align:justify;color:#eee}

/* services */
.service{position:absolute;text-align:center;width:260px}
.service h3{font-size:15px;font-weight:700;line-height:24px;letter-spacing:.3px}
.service p{font-size:13.5px;line-height:25px;color:#cfcfcf;margin-top:12px}
.service .more{display:inline-block;margin-top:10px;font-size:13.5px;color:var(--gold);text-decoration:underline}
.service.featured p{color:#3a2410}
.service.featured h3{color:#1a0f05}
.service.featured .more{color:#3a2410}

/* gallery */
.gallery-tile{position:absolute;width:223px;height:208px}
.btn-dark{position:absolute;left:526px;top:2987px;width:148px;height:42px;background:#000;color:#fff;font-weight:700;font-size:13.5px;display:flex;align-items:center;justify-content:center;border-radius:2px}

/* clients */
.client-card{position:absolute;top:3348px;width:213px;height:186px}
.client-card.active{outline:4px solid var(--gold);outline-offset:-4px}
.client-label{position:absolute;width:240px;text-align:center;font-size:14px;line-height:25px;font-weight:500}
.round-arrow{position:absolute;width:34px;height:34px;border-radius:50%;border:2px solid var(--gold);display:flex;align-items:center;justify-content:center}

/* contact */
.contact-bg{position:absolute;left:0;top:3690px;width:1200px;height:596px}
.form-label{position:absolute;font-size:15px;font-weight:700}
.field{position:absolute;background:#fff;border:1px solid #999;font-size:9.5px;color:#555;padding:8px 10px;font-weight:500}
.info-icon{position:absolute;left:782px;width:34px;height:34px;border-radius:50%;border:2px solid #fff;display:flex;align-items:center;justify-content:center}
.info-icon.filled{background:var(--gold);border-color:var(--gold)}
.info-text{position:absolute;left:832px;font-size:13px;line-height:17px;color:#eee}
.social{position:absolute;top:4091px;width:28px;height:28px;border-radius:50%;border:1.5px solid var(--gold)}
.social.on{background:var(--gold)}
.footer-rule{position:absolute;left:135px;top:4182px;width:930px;height:1px;background:#333}
.copyright{position:absolute;left:0;width:1200px;top:4222px;text-align:center;font-size:13px;color:#ddd}
</style>
</head>
<body>

<!-- header -->
<header class="site-header"></header>
<div class="brand"><span class="brand-dot"></span>Kestrada</div>
<a class="call-btn" href="#contact"><span class="call-icon">
  <svg width="14" height="14" viewBox="0 0 24 24"><path fill="#c8843a" d="M6.6 10.8a15 15 0 0 0 6.6 6.6l2.2-2.2c.3-.3.7-.4 1-.2 1.1.4 2.3.6 3.6.6.6 0 1 .4 1 1V20c0 .6-.4 1-1 1A17 17 0 0 1 3 4c0-.6.4-1 1-1h3.5c.6 0 1 .4 1 1 0 1.3.2 2.5.6 3.6.1.3 0 .7-.2 1z"/></svg>
</span>CALL US : +1 555 014 2290</a>
<nav class="main-nav">
  <a class="active" style="left:531px" href="#">HOME</a>
  <a style="left:620px" href="#about">ABOUT US</a>
  <a style="left:740px" href="#services">SERVICES</a>
  <a style="left:855px" href="#clients">CLIENTS</a>
  <a style="left:960px" href="#contact">CONTACT US</a>
</nav>

<!-- hero -->
<div class="hero-photo" role="img" aria-label="Engineer in safety vest inspecting large steel pipes on a construction site, seen through a pipe opening"></div>
<svg class="abs" style="left:0;top:600px" width="1200" height="280" viewBox="0 0 1200 280">
  <path d="M0 60 Q600 440 1200 60 L1200 280 L0 280Z" fill="#000"/>
  <path d="M0 60 Q300 230 600 240" fill="none" stroke="#c8843a" stroke-width="5"/>
  <path d="M600 240 Q900 230 1200 60" fill="none" stroke="#c8843a" stroke-width="2"/>
  <circle cx="600" cy="245" r="20" fill="#000" stroke="#c8843a" stroke-width="2"/>
  <path d="M600 235v18M593 247l7 7 7-7" fill="none" stroke="#c8843a" stroke-width="2"/>
</svg>
<h1 class="hero-title">BUILDING FOR COMMUNITIES.<br><span class="accent">TRUSTED BY GOVERNMENT,</span><br>HEALTHCARE &amp; EDUCATION</h1>
<a class="btn-gold" style="left:476px;top:413px;width:250px;height:42px" href="#services">EXPLORE OUR SERVICES</a>
<div class="hero-dots"><span class="on" style="top:399px"></span><span style="top:430px"></span><span style="top:463px"></span></div>

<!-- about -->
<div class="about-art" role="img" aria-label="Company emblem artwork with certification seal"></div>
<div class="about-badge" role="img" aria-label="Certification badge"></div>
<h2 class="section-title" style="left:642px;top:962px" id="about"><b>ABOUT</b> <span>US</span></h2>
<p class="about-text">Sed ut perspiciatis unde omnis iste natus error sit voluptatem accusantium doloremque laudantium, totam rem aperiam, eaque ipsa quae ab illo inventore veritatis et quasi architecto beatae vitae dicta sunt explicabo. Nemo enim ipsam voluptatem quia voluptas sit aspernatur aut odit aut fugit, sed quia consequuntur magni dolores eos qui ratione voluptatem sequi nesciunt. Neque porro quisquam est, qui dolorem ip qam quaerat voluptatem.</p>
<a class="btn-gold" style="left:642px;top:1350px;width:148px;height:41px" href="#about">READ MORE</a>

<div class="abs" style="left:140px;top:1510px;width:1060px;height:1px;background:#333"></div>
<div class="abs" style="left:135px;top:1506px;width:10px;height:10px;border-radius:50%;background:var(--gold)"></div>

<!-- services -->
<h2 class="section-title" style="left:158px;top:1638px" id="services"><b>OUR</b> <span>SERVICES</span></h2>
<div class="round-arrow" style="left:971px;top:1642px"><svg width="12" height="12" viewBox="0 0 12 12"><path d="M8 1 3 6l5 5" fill="none" stroke="#c8843a" stroke-width="2"/></svg></div>
<div class="round-arrow" style="left:1018px;top:1642px"><svg width="12" height="12" viewBox="0 0 12 12"><path d="m4 1 5 5-5 5" fill="none" stroke="#c8843a" stroke-width="2"/></svg></div>

<svg class="abs" style="left:0;top:1740px" width="1200" height="410" viewBox="0 1740 1200 410">
  <defs><linearGradient id="tri" x1="0" y1="0" x2="0" y2="1"><stop offset="0" stop-color="#f0c48c"/><stop offset="1" stop-color="#b0601f"/></linearGradient></defs>
  <path d="M5 1752 L446 1752 L225 2138Z" fill="none" stroke="#c8843a" stroke-width="1.5"/>
  <path d="M250 2138 L697 2138 L474 1752Z" fill="url(#tri)"/>
  <path d="M504 1752 L945 1752 L724 2138Z" fill="none" stroke="#c8843a" stroke-width="1.5"/>
  <path d="M754 2138 L1195 2138 L974 1752Z" fill="none" stroke="#c8843a" stroke-width="1.5"/>
  <g fill="none" stroke="#c8843a" stroke-width="2.5">
    <rect x="196" y="1995" width="44" height="32" rx="3"/><circle cx="218" cy="2011" r="8"/><path d="M208 2040h46"/>
    <rect x="698" y="1995" width="46" height="44"/><path d="M708 2030l28-26"/>
    <path d="M974 1858l-22 40h44z"/><path d="M974 1872v12M974 1889v3"/>
  </g>
  <g fill="none" stroke="#1a0f05" stroke-width="2.5"><path d="M452 1845h30l12 12v48h-42z"/><path d="M460 1865h26M460 1877h26"/></g>
</svg>
<div class="service" style="left:95px;top:1786px"><h3>ENVIRONMENTAL<br>REMEDIATION</h3><p>Sed ut perspiciatis unde omnis iste natus error sit voluptatem accusantium doloremque</p><a class="more" href="#">READ MORE</a></div>
<div class="service featured" style="left:344px;top:1938px"><h3>GENERAL<br>CONTRACTING</h3><p>Sed ut perspiciatis unde omnis iste natus error sit voluptatem accusantium doloremque</p><a class="more" href="#">READ MORE</a></div>
<div class="service" style="left:595px;top:1786px"><h3>DESIGN-BUILD<br>CONSTRUCTION</h3><p>Sed ut perspiciatis unde omnis iste natus error sit voluptatem accusantium doloremque</p><a class="more" href="#">READ MORE</a></div>
<div class="service" style="left:844px;top:1938px"><h3>DISASTER<br>RECOVERY</h3><p>Sed ut perspiciatis unde omnis iste natus error sit voluptatem accusantium doloremque</p><a class="more" href="#">READ MORE</a></div>

<!-- gallery -->
<svg class="abs" style="left:0;top:2260px" width="1200" height="880" viewBox="0 2260 1200 880">
  <defs><linearGradient id="gal" x1="0" y1="0" x2="0" y2="1"><stop offset="0" stop-color="#e8b070"/><stop offset=".5" stop-color="#cf8642"/><stop offset="1" stop-color="#a24e16"/></linearGradient></defs>
  <path d="M0 2463 Q520 2160 1200 2396 L1200 3138 L0 3138Z" fill="url(#gal)"/>
  <path d="M760 2270 Q1000 2310 1200 2396" fill="none" stroke="#9a4a16" stroke-width="8"/>
</svg>
<h2 class="section-title" style="left:400px;top:2428px;color:#000"><b>PROJECT</b> <span style="color:#000">GALLERY</span></h2>
<div class="gallery-tile" style="left:143px;top:2524px;background:linear-gradient(135deg,#b89a78,#5c4a3a)" role="img" aria-label="Worker kneeling beside a spill kit in a warehouse"></div>
<div class="gallery-tile" style="left:374px;top:2524px;background:linear-gradient(135deg,#2b3440,#1a2029)" role="img" aria-label="Yellow recovery ahead road sign under a dark sky"></div>
<div class="gallery-tile" style="left:602px;top:2524px;background:linear-gradient(135deg,#8eb0d8,#b39a74)" role="img" aria-label="Newly built family house"></div>
<div class="gallery-tile" style="left:834px;top:2524px;background:linear-gradient(135deg,#9aa3aa,#6d6258)" role="img" aria-label="Rescue workers on a rubble site"></div>
<div class="gallery-tile" style="left:143px;top:2742px;background:linear-gradient(135deg,#3d5a2c,#8a8a8a)" role="img" aria-label="Aerial view of a building site"></div>
<div class="gallery-tile" style="left:374px;top:2742px;background:linear-gradient(135deg,#8a8780,#4c4842)" role="img" aria-label="Responders clearing debris"></div>
<div class="gallery-tile" style="left:602px;top:2742px;background:linear-gradient(135deg,#3e6a2c,#c99a2a)" role="img" aria-label="Backhoe loader at work"></div>
<div class="gallery-tile" style="left:834px;top:2742px;background:linear-gradient(135deg,#e4e4e4,#b07a52)" role="img" aria-label="Construction team reviewing plans"></div>
<div class="abs" style="left:464px;top:2604px;width:40px;height:40px;border-radius:50%;background:#111;color:#fff;font-size:20px;display:flex;align-items:center;justify-content:center">+</div>
<a class="btn-dark" href="#">VIEW MORE</a>

<!-- clients -->
<h2 class="section-title" style="left:391px;top:3246px" id="clients"><b>FEATURED</b> <span>CLIENTS</span></h2>
<div class="round-arrow" style="left:85px;top:3424px"><svg width="12" height="12" viewBox="0 0 12 12"><path d="M8 1 3 6l5 5" fill="none" stroke="#c8843a" stroke-width="2"/></svg></div>
<div class="round-arrow" style="left:1081px;top:3424px"><svg width="12" height="12" viewBox="0 0 12 12"><path d="m4 1 5 5-5 5" fill="none" stroke="#c8843a" stroke-width="2"/></svg></div>
<div class="client-card active" style="left:148px;background:linear-gradient(#6d7f95,#c9925a)" role="img" aria-label="Service members and helicopter at dusk"></div>
<div class="abs" style="left:236px;top:3423px;width:36px;height:36px;border-radius:50%;background:var(--gold);color:#fff;font-size:20px;display:flex;align-items:center;justify-content:center">+</div>
<div class="client-card" style="left:378px;background:linear-gradient(#7aa4d4,#8a9a6a)" role="img" aria-label="Government office buildings"></div>
<div class="client-card" style="left:609px;background:linear-gradient(#e8eef2,#a9bccb)" role="img" aria-label="Hospital ward"></div>
<div class="client-card" style="left:839px;background:linear-gradient(#6ea0de,#d6d0c8)" role="img" aria-label="School building"></div>
<div class="client-label" style="left:134px;top:3551px">PMX</div>
<div class="client-label" style="left:364px;top:3551px">STATE AND LOCAL GOV'T<br>AGENCIES</div>
<div class="client-label" style="left:594px;top:3551px">HOSPITALS</div>
<div class="client-label" style="left:825px;top:3551px">SCHOOLS</div>

<!-- contact -->
<svg class="contact-bg" viewBox="0 3690 1200 596">
  <path d="M0 3894 Q560 3560 1200 3780 L1200 4286 L0 4286Z" fill="#1a1a1a"/>
  <path d="M560 3700 Q900 3700 1200 3780" fill="none" stroke="#c8843a" stroke-width="6"/>
</svg>
<h2 class="section-title" style="left:468px;top:3800px" id="contact"><b>CONTACT</b> <span>US</span></h2>
<div class="form-label" style="left:166px;top:3896px">Get In Touch:</div>
<div class="field" style="left:168px;top:3937px;width:266px;height:30px">NAME :</div>
<div class="field" style="left:444px;top:3937px;width:267px;height:30px">PHONE :</div>
<div class="field" style="left:168px;top:3979px;width:543px;height:28px">EMAIL :</div>
<div class="field" style="left:168px;top:4019px;width:543px;height:66px">MESSAGE :</div>
<a class="btn-gold" style="left:632px;top:4103px;width:79px;height:29px;border-radius:15px;font-size:11px" href="#">SUBMIT</a>

<div class="form-label" style="left:780px;top:3896px">Contact Information</div>
<div class="info-icon" style="top:3938px"><svg width="14" height="16" viewBox="0 0 14 16"><path d="M7 15s5-5 5-9A5 5 0 0 0 2 6c0 4 5 9 5 9z" fill="none" stroke="#fff" stroke-width="1.6"/><circle cx="7" cy="6" r="1.8" fill="#fff"/></svg></div>
<div class="info-text" style="top:3946px">418 Harlow Ridge Road, Suite 12,<br>Larkfield</div>
<div class="info-icon filled" style="top:3986px"><svg width="14" height="14" viewBox="0 0 24 24"><path fill="#fff" d="M6.6 10.8a15 15 0 0 0 6.6 6.6l2.2-2.2c.3-.3.7-.4 1-.2 1.1.4 2.3.6 3.6.6.6 0 1 .4 1 1V20c0 .6-.4 1-1 1A17 17 0 0 1 3 4c0-.6.4-1 1-1h3.5c.6 0 1 .4 1 1 0 1.3.2 2.5.6 3.6.1.3 0 .7-.2 1z"/></svg></div>
<div class="info-text" style="top:3995px;font-weight:700">Phone : +1 555 014 2290</div>
<div class="info-icon" style="top:4032px"><svg width="14" height="12" viewBox="0 0 14 12"><rect x="1" y="1" width="12" height="10" rx="1" fill="#fff"/><path d="M1 2l6 5 6-5" fill="none" stroke="#1a1a1a" stroke-width="1.4"/></svg></div>
<div class="info-text" style="top:4041px">hello@kestrada-build.com</div>
<div class="social" style="left:781px"></div>
<div class="social on" style="left:816px"></div>
<div class="social" style="left:850px"></div>
<div class="social" style="left:885px"></div>

<div class="footer-rule"></div>
<div class="copyright">Copyrights © 2025, Kestrada LLC. All Rights Reserved. &nbsp;|&nbsp; Privacy policy</div>

</body>
</html>
```